Garlic Farm for Farm Sales/Restaurant sales

Need a professional, but appealing to agriculture world. We are selling 27 kinds of Organic Garlic from a farm in Simla,CO. I have uploaded logo and business information-we are going to need a template, because I will need to use it for four separate people.
-We are trying to appeal to Farm to table restaurants
-As well as growers/farmers

Target Market(s)

Agriculture Sales/Restaurants-Organic

Industry/Entity Type

Agriculture

Contact Information for Business Card

Want it to look more unique then your average kelto stock card- I want it to look amazing

Font styles to use
Sans Serif

Colors
0455a3
ec1f27
fbed22
ffffff

Requirements
Must have
• Just be creative
Nice to have
• Colorful
Should not have
• plain

```html
<!DOCTYPE html>
<html lang="en">
<head>
<meta charset="utf-8">
<title>Summit Crest Garlic – Business Card</title>
<link href="https://fonts.googleapis.com/css2?family=Arimo:wght@400;700&display=swap" rel="stylesheet">
<style>
  :root {
    --brand-blue: #0455a3;
    --brand-red: #ec1f27;
    --brand-yellow: #fbed22;
    --paper: #ffffff;
    --ink: #1a1a1a;
    --backdrop: #e9e6e1;
  }
  * { box-sizing: border-box; margin: 0; padding: 0; }
  html, body {
    width: 1200px; height: 892px; overflow: hidden;
    background: var(--backdrop);
    font-family: "Arimo", Arial, sans-serif;
  }
  .canvas { position: relative; width: 1200px; height: 892px; }

  .card {
    position: absolute;
    background: var(--paper);
    box-shadow: 0 10px 28px rgba(0,0,0,0.18);
    overflow: hidden;
  }

  /* Front */
  .card-front { left: 170px; top: 126px; width: 360px; height: 640px; }
  .front-brand {
    position: absolute; top: 92px; left: 0; right: 0;
    display: flex; flex-direction: column; align-items: center; gap: 18px;
  }
  .brand-dot {
    width: 64px; height: 64px; border-radius: 50%;
    background: var(--brand-red);
  }
  .brand-name {
    color: var(--brand-blue); font-weight: 400;
    font-size: 30px; letter-spacing: 2px; text-transform: uppercase;
    text-align: center; line-height: 1.15;
  }
  .person { position: absolute; top: 300px; left: 44px; right: 30px; }
  .person-name {
    color: var(--brand-red); font-weight: 700; font-size: 34px; line-height: 1;
  }
  .person-title { color: var(--ink); font-size: 19px; margin-top: 4px; }

  .contact { position: absolute; top: 388px; left: 44px; right: 20px; color: var(--ink); font-size: 17px; line-height: 23px; }
  .contact-line { display: flex; align-items: center; gap: 8px; }
  .contact-icon { width: 16px; height: 16px; flex: none; fill: var(--brand-red); }
  .contact-email { margin-top: 2px; }
  .contact-address { margin-top: 10px; }

  .web-band {
    position: absolute; left: 0; right: 0; bottom: 0; height: 92px;
    background: var(--brand-red);
    display: flex; align-items: center; justify-content: center;
    color: var(--paper); font-size: 26px; letter-spacing: 0.5px;
  }

  /* Back */
  .card-back {
    left: 580px; top: 266px; width: 460px; height: 300px;
    display: flex; align-items: center; justify-content: center; gap: 22px;
  }
  .card-back .brand-dot { width: 56px; height: 56px; }
  .card-back .brand-name { font-size: 28px; text-align: left; }
</style>
</head>
<body>
<main class="canvas">

  <section class="card card-front" aria-label="Business card front">
    <div class="front-brand">
      <span class="brand-dot" aria-hidden="true"></span>
      <p class="brand-name">Summit Crest<br>Garlic</p>
    </div>

    <div class="person">
      <h1 class="person-name">Dale Marsh</h1>
      <p class="person-title">Product Specialist</p>
    </div>

    <div class="contact">
      <p class="contact-line">
        <svg class="contact-icon" viewBox="0 0 16 16" aria-hidden="true"><rect x="4" y="0.5" width="8" height="15" rx="1.5"/><rect x="5.3" y="2.3" width="5.4" height="8.5" fill="#fff"/><circle cx="8" cy="13" r="1" fill="#fff"/></svg>
        555-214-3307
      </p>
      <p class="contact-line">
        <svg class="contact-icon" viewBox="0 0 16 16" aria-hidden="true"><path d="M1 5c0-2 3-3.5 7-3.5S15 3 15 5v1.5h-3.5V4.8c-2.2-.6-4.8-.6-7 0v1.7H1z"/><path d="M3 9l2-2.5h6L13 9v5.5H3z"/><circle cx="8" cy="11" r="1.6" fill="#fff"/></svg>
        555-214-3390
      </p>
      <p class="contact-line">
        <svg class="contact-icon" viewBox="0 0 16 16" aria-hidden="true"><rect x="4" y="1" width="8" height="5"/><rect x="1" y="6" width="14" height="6.5" rx="1"/><rect x="4" y="10" width="8" height="5" fill="#fff" stroke="#ec1f27" stroke-width="1.2"/></svg>
        555-214-3391
      </p>
      <p class="contact-email">dmarsh@fernvalegroup.com</p>
      <p class="contact-address">1418 Orchard Lane<br>Pinebrook, AL 35000</p>
    </div>

    <div class="web-band">www.fernvalegroup.com</div>
  </section>

  <section class="card card-back" aria-label="Business card back">
    <span class="brand-dot" aria-hidden="true"></span>
    <p class="brand-name">Summit Crest<br>Garlic</p>
  </section>

</main>
</body>
</html>
```